Business Card Design

I already have a company logo for my company. I have a logo for the manufacturer we represent. I want a professional business card design.

```html
<!DOCTYPE html>
<html lang="en">
<head>
<meta charset="UTF-8">
<title>Beacon Alert Co – Business Card</title>
<link href="https://fonts.googleapis.com/css2?family=Montserrat:wght@500;800&family=Poppins:wght@400;500&display=swap" rel="stylesheet">
<style>
  :root {
    --backdrop: #d6d6d6;
    --alert-red: #e30d1c;
    --alert-orange: #e8591a;
    --alert-amber: #dea90f;
    --ink: #1f1f1f;
    --paper: #ffffff;
    --band: rgba(227, 13, 28, 0.07);
  }
  * { box-sizing: border-box; margin: 0; padding: 0; }
  html, body {
    width: 1200px; height: 900px; overflow: hidden;
    background: var(--backdrop);
  }
  .canvas { position: relative; width: 1200px; height: 900px; }

  .card {
    position: absolute;
    width: 560px; height: 320px;
    border-radius: 26px;
    overflow: hidden;
    box-shadow: 0 6px 18px rgba(0,0,0,0.25);
  }

  /* Front */
  .card--front {
    left: 50px; top: 110px;
    background: linear-gradient(20deg, var(--alert-red) 0%, var(--alert-orange) 55%, var(--alert-amber) 100%);
    display: flex; align-items: center; justify-content: center; gap: 16px;
  }
  .brand-dot {
    width: 22px; height: 22px; border-radius: 50%;
    background: var(--paper);
  }
  .card--front .brand-name {
    font-family: "Montserrat", sans-serif;
    font-weight: 800;
    font-size: 44px;
    letter-spacing: 2px;
    color: var(--paper);
    text-transform: uppercase;
  }

  /* Back */
  .card--back {
    left: 590px; top: 470px;
    background: var(--paper);
  }
  .back-bands { position: absolute; inset: 0; }
  .back-brand {
    position: absolute; left: 200px; top: 40px;
    display: flex; align-items: center; gap: 10px;
  }
  .back-brand .brand-dot { width: 14px; height: 14px; background: var(--alert-red); }
  .back-brand .brand-name {
    font-family: "Montserrat", sans-serif;
    font-weight: 800; font-size: 24px;
    letter-spacing: 1px; color: var(--alert-red);
    text-transform: uppercase;
  }
  .person { position: absolute; left: 40px; top: 140px; }
  .person-name {
    font-family: "Montserrat", sans-serif;
    font-weight: 800; font-size: 28px; letter-spacing: 1.5px;
    color: var(--alert-red); text-transform: uppercase;
  }
  .person-title {
    font-family: "Poppins", sans-serif;
    font-size: 17px; color: var(--ink); margin-top: 2px;
  }
  .contact-list {
    position: absolute; left: 40px; top: 222px;
    list-style: none;
    font-family: "Poppins", sans-serif; font-size: 16px; color: var(--ink);
  }
  .contact-list li { display: flex; align-items: center; gap: 10px; height: 26px; }
  .contact-list svg { width: 16px; height: 16px; fill: var(--alert-red); flex: none; }
  .contact-list .accent { color: var(--alert-red); }
  .address {
    position: absolute; right: 34px; top: 170px;
    text-align: right;
    font-family: "Poppins", sans-serif; font-size: 15px; line-height: 1.45;
    color: var(--ink);
  }
</style>
</head>
<body>
<main class="canvas">

  <section class="card card--front" aria-label="Card front">
    <span class="brand-dot"></span>
    <span class="brand-name">Beacon Alert Co</span>
  </section>

  <section class="card card--back" aria-label="Card back">
    <svg class="back-bands" viewBox="0 0 560 320" aria-hidden="true">
      <polygon points="250,150 560,20 560,60 290,170" fill="var(--band)"/>
      <polygon points="270,200 560,80 560,120 310,220" fill="var(--band)"/>
      <polygon points="300,250 560,140 560,175 335,265" fill="var(--band)"/>
    </svg>

    <div class="back-brand">
      <span class="brand-dot"></span>
      <span class="brand-name">Beacon Alert Co</span>
    </div>

    <div class="person">
      <p class="person-name">Daniel Hayes</p>
      <p class="person-title">Managing Director</p>
    </div>

    <ul class="contact-list">
      <li>
        <svg viewBox="0 0 24 24"><path d="M6.6 10.8a15 15 0 0 0 6.6 6.6l2.2-2.2a1 1 0 0 1 1-.25 11.4 11.4 0 0 0 3.6.57 1 1 0 0 1 1 1V20a1 1 0 0 1-1 1A17 17 0 0 1 3 4a1 1 0 0 1 1-1h3.5a1 1 0 0 1 1 1c0 1.25.2 2.45.57 3.57a1 1 0 0 1-.25 1z"/></svg>
        044-555 018 342
      </li>
      <li>
        <svg viewBox="0 0 24 24"><path d="M2 5h20v14H2z M2 5l10 8 10-8" fill="none" stroke="var(--alert-red)" stroke-width="2"/></svg>
        info@beaconalert.co
      </li>
      <li>
        <svg viewBox="0 0 24 24"><circle cx="12" cy="12" r="9" fill="none" stroke="var(--alert-red)" stroke-width="2"/><path d="M3 12h18M12 3c3 3 3 15 0 18M12 3c-3 3-3 15 0 18" fill="none" stroke="var(--alert-red)" stroke-width="1.6"/></svg>
        <span>www.<span class="accent">beaconalert</span>.co</span>
      </li>
    </ul>

    <address class="address" style="font-style:normal">
      88, Harbor Row Suite 4<br>
      10452, Eastland
    </address>
  </section>

</main>
</body>
</html>
```